Logistics Website Design

See website https://tqfreightglobal.com for theme and color details. Need the site to be re-done and reflect some of the designs shown in this list here: https://pixelvane.com/tags/logistics-company-website

Target Market(s)

Logistics & Transportation

Industry/Entity Type

Logistics and Supply Chain

Coding

Number of Pages Required

5+ page

Requirements
Must have
• Colors must match theme of logo. Looking for a sleek, interactive design.

```html
<!DOCTYPE html>
<html lang="en">
<head>
<meta charset="utf-8">
<title>TQ Freight Global</title>
<link href="https://fonts.googleapis.com/css2?family=Poppins:ital,wght@0,400;0,500;0,600;0,700;1,700;1,800&display=swap" rel="stylesheet">
<style>
:root{
  --night:#1d0605;
  --brown:#6e2a14;
  --rust:#7a2611;
  --orange:#ec6a3d;
  --orange-deep:#d9552a;
  --white:#ffffff;
  --ink:#1a1a1a;
}
*{margin:0;padding:0;box-sizing:border-box}
html,body{width:1200px;height:3421px;overflow:hidden}
body{position:relative;font-family:'Poppins',sans-serif;background:var(--white);color:var(--ink)}
.abs{position:absolute}
.btn{position:absolute;display:flex;align-items:center;justify-content:center;border-radius:40px;background:linear-gradient(180deg,#f07a4b,var(--orange-deep));color:var(--white);font-weight:700;text-transform:uppercase;letter-spacing:.3px}
.heading{font-weight:800;font-style:italic;text-transform:uppercase;line-height:1.1}
.accent{color:var(--orange)}

/* header & hero */
.hero{left:0;top:0;width:1200px;height:720px;background:var(--night)}
.hero-photo{left:0;top:82px;width:1130px;height:570px;border-bottom-right-radius:150px;background:linear-gradient(120deg,#1b1c20 0%,#4b5560 45%,#9aa5ae 70%,#6b747c 100%)}
.hero-shade{left:0;top:82px;width:1130px;height:570px;border-bottom-right-radius:150px;background:linear-gradient(90deg,rgba(0,0,0,.65),rgba(0,0,0,0) 60%)}
.brand-badge{left:90px;top:9px;width:154px;height:154px;border-radius:50%;background:var(--white);display:flex;align-items:center;justify-content:center}
.brand-name{font-weight:700;font-size:22px;color:var(--orange-deep);text-align:center;line-height:1.1}
.nav{left:398px;top:30px;display:flex;gap:0;font-size:14px;font-weight:600;color:var(--white)}
.nav a{position:absolute;white-space:nowrap;color:var(--white);text-decoration:none}
.nav .current{color:var(--orange);font-style:italic;border-bottom:2px solid var(--orange);padding-bottom:2px}
.hero-title{left:77px;top:245px;font-size:45px;color:var(--white)}
.hero-sub{left:77px;top:346px;font-size:25px;font-weight:500;color:var(--white);line-height:1.35}

/* about */
.about-photo{left:0;top:799px;width:587px;height:414px;border-radius:0 210px 210px 0/0 207px 207px 0;background:linear-gradient(135deg,#c9d2da 0%,#8f99a2 45%,#5d646b 100%)}
.about-title{left:618px;top:792px;font-size:40px;color:var(--ink)}
.about-tag{left:618px;top:893px;font-size:25px;font-weight:700;font-style:italic;color:var(--rust)}
.about-text{left:618px;top:933px;width:505px;font-size:14.5px;line-height:29px;color:#222}

/* services */
.services{left:78px;top:1304px;width:1122px;height:569px;background:var(--brown);border-top-left-radius:95px}
.services-title{left:106px;top:1372px;font-size:40px;color:var(--white)}
.arrow{top:1386px;width:22px;height:22px;border-radius:50%;display:flex;align-items:center;justify-content:center}
.card-photo{top:1443px;width:316px;height:220px;border-radius:18px}
.card-title{top:1681px;font-size:17.5px;font-weight:800;font-style:italic;color:var(--white);text-transform:uppercase}
.card-text{top:1706px;width:316px;font-size:14px;line-height:23px;color:#f6e6df}

/* industries */
.ind-title{left:0;top:1926px;width:1200px;text-align:center;font-size:40px;color:var(--ink)}
.ind-label{font-size:21px;font-weight:800;font-style:italic;color:var(--rust);text-transform:uppercase;white-space:nowrap}

/* quote */
.quote{left:0;top:2527px;width:1200px;height:577px;background:var(--brown)}
.quote-photo{left:0;top:2609px;width:587px;height:414px;border-top-right-radius:200px;background:linear-gradient(160deg,#2f3a43 0%,#7c8790 45%,#3a3126 100%)}
.quote-title{left:621px;top:2600px;font-size:40px;color:var(--white)}
.field{left:618px;width:511px;height:61px;border-radius:31px;background:var(--white);font-size:15px;color:#222;padding-left:26px;display:flex;align-items:center}

/* footer */
.foot-head{top:3166px;font-size:18.5px;font-weight:700;color:var(--rust);text-transform:uppercase}
.foot-link{font-size:14px;font-weight:500;color:#222;text-transform:uppercase}
.social{top:3216px;width:20px;height:20px;border-radius:50%;background:var(--rust)}
</style>
</head>
<body>

<!-- header + hero -->
<section class="abs hero"></section>
<div class="abs hero-photo" role="img" aria-label="Photo of white trucks parked at a warehouse loading dock under a stormy sky"></div>
<div class="abs hero-shade"></div>

<div class="abs brand-badge"><div class="brand-name">TQ Freight</div></div>

<nav class="abs nav">
  <a class="current" style="left:0;top:0">HOME</a>
  <a style="left:85px;top:0">ABOUT US</a>
  <a style="left:200px;top:0">SERVICES INDUSTRIES</a>
  <a style="left:403px;top:0">CONTACT US</a>
</nav>
<div class="btn" style="left:931px;top:19px;width:198px;height:43px;font-size:14px">Request a Quote</div>

<h1 class="abs heading hero-title">Delivering Strength<br>in Every Mile</h1>
<p class="abs hero-sub">Secure and reliable transportation for<br>all your cargo needs.</p>
<div class="btn" style="left:78px;top:433px;width:197px;height:43px;font-size:14px">Request a Quote</div>

<!-- about -->
<div class="abs about-photo" role="img" aria-label="Photo of a white semi truck backed up to a warehouse loading bay"></div>
<h2 class="abs heading about-title">About <span class="accent">TQ Freight<br>Global</span>™</h2>
<p class="abs about-tag">Keeping Your Supply Chain Moving</p>
<p class="abs about-text">We deliver a comprehensive range of open-deck and specialized transportation services—including flatbed, step deck, heavy haul, and over-dimensional freight solutions. Backed by years of experience, a trusted nationwide carrier network, and a strong safety-first culture, we provide reliable, adaptable logistics support built around the unique requirements of every load.</p>
<div class="btn" style="left:618px;top:1152px;width:178px;height:61px;font-size:18px">Read More</div>

<!-- services -->
<section class="abs services"></section>
<h2 class="abs heading services-title">Our <span class="accent">Services</span></h2>
<div class="abs arrow" style="left:1078px;background:var(--white)"><svg width="12" height="12" viewBox="0 0 12 12"><path d="M10 6H2M5.5 2.5 2 6l3.5 3.5" stroke="#6e2a14" stroke-width="2" fill="none"/></svg></div>
<div class="abs arrow" style="left:1108px;background:var(--orange)"><svg width="12" height="12" viewBox="0 0 12 12"><path d="M2 6h8M6.5 2.5 10 6 6.5 9.5" stroke="#fff" stroke-width="2" fill="none"/></svg></div>

<div class="abs card-photo" style="left:110px;background:linear-gradient(160deg,#b9c3c9,#7b6a5a 60%,#3d3530)" role="img" aria-label="Photo of a flatbed truck loaded with lumber"></div>
<h3 class="abs card-title" style="left:110px">Flatbed Transportation</h3>
<p class="abs card-text" style="left:110px">From routine shipments to oversized and heavy-haul loads, we handle freight requiring proper securement, regulatory knowledge, and consistent on-time execution.</p>

<div class="abs card-photo" style="left:462px;background:linear-gradient(170deg,#9fc0db,#d8e4ea 45%,#3f7a3a 70%,#5b5f63)" role="img" aria-label="Photo of a green step deck truck by a mountain lake"></div>
<h3 class="abs card-title" style="left:462px">Step Deck Transportation</h3>
<p class="abs card-text" style="left:462px">Our step deck trucking services support tall, heavy, and specialized freight that requires additional height clearance and flexible loading options.</p>

<div class="abs card-photo" style="left:813px;background:linear-gradient(170deg,#d9dde0,#9aa3aa 50%,#e8eaec)" role="img" aria-label="Photo of a row of white delivery vans at a depot"></div>
<h3 class="abs card-title" style="left:813px">Dry Van Transportation</h3>
<p class="abs card-text" style="left:813px">From consumer goods to industrial materials, our dry van services provide the space, security, and consistency you need coast to coast.</p>

<!-- industries -->
<h2 class="abs heading ind-title">Industries <span class="accent">Served</span></h2>
<svg class="abs" style="left:0;top:1980px" width="1200" height="460" viewBox="0 1980 1200 460">
  <path d="M395 2155 A210 210 0 1 0 808 2155" fill="none" stroke="#ec8a66" stroke-width="7"/>
  <circle cx="602" cy="2196" r="195" fill="#3a0e08"/>
  <circle cx="395" cy="2155" r="12" fill="#ec8a66"/>
  <circle cx="808" cy="2155" r="12" fill="#ec8a66"/>
  <circle cx="437" cy="2328" r="12" fill="#ec8a66"/>
  <circle cx="768" cy="2328" r="12" fill="#ec8a66"/>
  <circle cx="602" cy="2406" r="12" fill="#ec8a66"/>
  <text x="602" y="2206" text-anchor="middle" font-family="Poppins, sans-serif" font-weight="700" font-size="40" fill="#ec6a3d">TQ Freight</text>
</svg>
<div class="abs ind-label" style="right:839px;top:2142px">Food &amp; Beverages</div>
<div class="abs ind-label" style="left:841px;top:2142px">Government</div>
<div class="abs ind-label" style="right:794px;top:2316px">E-Commerce &amp; Retails</div>
<div class="abs ind-label" style="left:800px;top:2316px">Pharma &amp; Healthcare</div>
<div class="abs ind-label" style="left:0;width:1204px;text-align:center;top:2433px">Manufacturing</div>

<!-- quote -->
<section class="abs quote"></section>
<div class="abs quote-photo" role="img" aria-label="Photo of two white box trucks parked at loading docks"></div>
<h2 class="abs heading quote-title">Request <span class="accent">a Quote</span></h2>
<div class="abs field" style="top:2671px">Name</div>
<div class="abs field" style="top:2743px">Email Address</div>
<div class="abs field" style="top:2815px">Phone No</div>
<div class="abs field" style="top:2887px">Message</div>
<div class="btn" style="left:618px;top:2962px;width:178px;height:61px;font-size:18px">Submit</div>

<!-- footer -->
<div class="abs" style="left:120px;top:3172px;width:160px;height:140px;display:flex;align-items:center;justify-content:center"><div class="brand-name">TQ Freight</div></div>
<p class="abs" style="left:60px;width:280px;top:3336px;text-align:center;font-size:13px;line-height:20px;color:#222">Copyright © 2026 Company Name<br>All rights reserved</p>

<h4 class="abs foot-head" style="left:372px">Quick Links</h4>
<div class="abs foot-link" style="left:372px;top:3210px">Home</div>
<div class="abs foot-link" style="left:372px;top:3246px">About Us</div>
<div class="abs foot-link" style="left:372px;top:3282px">Services</div>
<div class="abs foot-link" style="left:372px;top:3318px">Industries</div>
<div class="abs foot-link" style="left:372px;top:3354px">Contact Us</div>

<h4 class="abs foot-head" style="left:600px">Services</h4>
<div class="abs foot-link" style="left:600px;top:3210px">Flatbed Transportation</div>
<div class="abs foot-link" style="left:600px;top:3246px">Step Deck Transportation</div>
<div class="abs foot-link" style="left:600px;top:3282px">Dry Van Transportation</div>
<div class="abs foot-link" style="left:600px;top:3318px">Heavy Haul Transportation</div>

<h4 class="abs foot-head" style="left:911px">Follow Us</h4>
<div class="abs social" style="left:905px"></div>
<div class="abs social" style="left:937px"></div>
<div class="abs social" style="left:976px"></div>
<div class="abs social" style="left:1017px"></div>
<div class="abs social" style="left:1058px"></div>

</body>
</html>
```